Vernac Law Business cards and stationary design project

We are looking for a stationary design for business cards (double sided), 8x10, 5x7, and legal and standard envelopes.

We would like the design to match the logo that we have already.
Color palate preferred is Teal, White, grey and any others that will look good for a professional law firm.

We would like this statement: "RELATIONSHIPS. RESPECT. RESULT" to be on the back of the business cards and maybe on the stationary if it looks good.

Please see link to website for more information: www.vernac-law.example

Target Market(s)

Potential clients that need Attorney services.

Industry/Entity Type

Law Firm

Contact Information for Business Card

We would like the front and back to be two different colors. Current business cards are teal front, grey back and are a vertical design. We are open to options with colors.

Font styles to use
Serif

Colors
33a6d7
33b8a4
b9b9b9
5c5c5c

Requirements
Must have
• Logo supplied needs to go on the card and stationary.
• Match website color palate, www.vernac-law.example
• Be professional and not too wordy.
• Criminal Law, Civil Litigation, Personal Injury, Restraining Orders need to be on the card.
Nice to have
• RELATIONSHIPS. RESPECT. RESULTS. on the back of the card.
Should not have
• Not be too busy/wordy or too flashy.

```html
<!DOCTYPE html>
<html lang="en">
<head>
<meta charset="utf-8">
<title>Vernac Law — Business Card</title>
<link href="https://fonts.googleapis.com/css2?family=Cinzel:wght@400;500&family=Tinos&display=swap" rel="stylesheet">
<style>
  :root {
    --teal: #10889a;
    --ink: #4a4a4a;
    --paper: #ffffff;
    --backdrop: #3b3b3b;
  }
  * { margin: 0; padding: 0; box-sizing: border-box; }
  html, body { width: 1105px; height: 1200px; overflow: hidden; }
  body { background: var(--backdrop); position: relative; font-family: "Tinos", serif; }

  .card {
    position: absolute;
    left: 196px;
    width: 719px;
    height: 412px;
    overflow: hidden;
  }
  .card--front { top: 146px; background: var(--paper); }
  .card--back { top: 602px; background: var(--teal); }

  .edge-tab {
    position: absolute;
    left: -14px; top: 33px;
    width: 26px; height: 58px;
    border-radius: 10px;
    background: var(--teal);
  }
  .holder { position: absolute; left: 37px; top: 30px; }
  .holder-name {
    font-family: "Cinzel", serif;
    font-weight: 500;
    font-size: 33px;
    color: var(--teal);
    letter-spacing: 1px;
    line-height: 1.1;
  }
  .holder-title {
    font-family: "Cinzel", serif;
    font-size: 21px;
    color: var(--ink);
    letter-spacing: 1.5px;
    margin-top: 2px;
  }

  .firm-name {
    position: absolute;
    right: 36px; top: 130px;
    display: flex; align-items: center; gap: 12px;
    font-family: "Cinzel", serif;
    font-weight: 400;
    font-size: 33px;
    color: var(--teal);
    letter-spacing: 1.5px;
  }
  .firm-name .dot { width: 14px; height: 14px; border-radius: 50%; background: var(--teal); }

  .contact { position: absolute; left: 38px; top: 294px; list-style: none; }
  .contact li {
    display: flex; align-items: center; gap: 14px;
    font-size: 20px; color: var(--ink);
    height: 30px;
  }
  .contact svg { width: 18px; height: 18px; fill: var(--teal); flex: none; }

  .practice {
    position: absolute; right: 36px; top: 296px;
    text-align: right; list-style: none;
    font-size: 20px; color: var(--ink);
    line-height: 27px;
  }

  .back-name {
    position: absolute; left: 0; right: 0; top: 160px;
    text-align: center;
    font-family: "Cinzel", serif;
    font-size: 56px;
    color: var(--paper);
    letter-spacing: 3px;
  }
  .tagline {
    position: absolute; left: 0; right: 0; top: 354px;
    text-align: center;
    font-family: "Cinzel", serif;
    font-size: 22px;
    color: var(--paper);
    letter-spacing: 1.5px;
  }
</style>
</head>
<body>
  <section class="card card--front">
    <div class="edge-tab"></div>
    <div class="holder">
      <h1 class="holder-name">Dana Merrow</h1>
      <p class="holder-title">Trial Lawyer</p>
    </div>
    <div class="firm-name"><span class="dot"></span>Vernac Law</div>

    <ul class="contact">
      <li>
        <svg viewBox="0 0 24 24" aria-hidden="true"><path d="M6.6 10.8a15.1 15.1 0 0 0 6.6 6.6l2.2-2.2c.3-.3.7-.4 1-.2 1.1.4 2.3.6 3.6.6.6 0 1 .4 1 1V20c0 .6-.4 1-1 1A17 17 0 0 1 3 4c0-.6.4-1 1-1h3.5c.6 0 1 .4 1 1 0 1.3.2 2.5.6 3.6.1.3 0 .7-.2 1z"/></svg>
        (555) 014-2380
      </li>
      <li>
        <svg viewBox="0 0 24 24" aria-hidden="true"><path d="M2 5h20v14H2z M2 5l10 7 10-7" /><path d="M3 6.5l9 6.3 9-6.3V18H3z" fill="#fff" opacity="0"/></svg>
        dana@vernac-law.example
      </li>
      <li>
        <svg viewBox="0 0 24 24" aria-hidden="true"><circle cx="12" cy="12" r="10"/><path d="M2 12h20M12 2c3 3 3 17 0 20M12 2c-3 3-3 17 0 20" stroke="#fff" stroke-width="1.4" fill="none"/></svg>
        www.vernac-law.example
      </li>
    </ul>

    <ul class="practice">
      <li>Criminal Law</li>
      <li>Civil Litigation/Personal Injury</li>
      <li>Restraining</li>
    </ul>
  </section>

  <section class="card card--back">
    <div class="back-name">Vernac Law</div>
    <p class="tagline">RELATIONSHIPS. RESPECT. RESULTS.</p>
  </section>
</body>
</html>
```